Card design for orthopaedic surgeons working as The Brightwater Joint Centre

Business cards, letterhead

Colors

Designer to choose colors to be used in the design.

Requirements
Must have
• Late addition.
• Cards letterhead must have logos of
• Crestmoor Lindell College of Surgeons
• Varenwood Bone Health Association
Nice to have
• Back of card to have space for appointment time to be added by hand and some blank space for writing incidental other notes.

```html
<!DOCTYPE html>
<html lang="en">
<head>
<meta charset="utf-8">
<title>The Brightwater Joint Centre – Business Cards</title>
<link href="https://fonts.googleapis.com/css2?family=Montserrat:wght@400;500;600&family=Open+Sans:wght@300;400;600;700&display=swap" rel="stylesheet">
<style>
  :root {
    --backdrop: #2b2c2e;
    --card: #ffffff;
    --brand-blue: #3ea3f0;
    --deep-teal: #0c4b66;
    --navy: #0d2f4a;
    --ink: #3a3f44;
    --muted: #6b7075;
    --rule: #9aa0a5;
    --logo-light: #8fcaf5;
  }
  * { box-sizing: border-box; margin: 0; padding: 0; }
  html, body { width: 1200px; height: 960px; overflow: hidden; }
  body { background: var(--backdrop); position: relative; font-family: "Open Sans", sans-serif; }

  .card {
    position: absolute;
    width: 700px; height: 400px;
    background: var(--card);
    overflow: hidden;
  }
  .card--appointment { left: 70px; top: 60px; }
  .card--contact { left: 430px; top: 500px; }

  /* Appointment side */
  .brand-name {
    font-family: "Open Sans", sans-serif;
    font-weight: 400;
    color: var(--brand-blue);
    display: flex; align-items: center; gap: 10px;
    white-space: nowrap;
  }
  .brand-name .mark { width: 14px; height: 14px; border-radius: 50%; background: currentColor; flex: none; }
  .card--appointment .brand-name { position: absolute; left: 150px; top: 52px; font-size: 30px; }

  .appt-form { position: absolute; left: 50px; top: 140px; right: 50px; font-family: "Montserrat", sans-serif; color: var(--ink); }
  .appt-row { display: flex; align-items: flex-end; gap: 8px; height: 40px; font-size: 14px; font-weight: 500; letter-spacing: .5px; }
  .appt-row .fill { flex: 1; border-bottom: 1.5px dotted var(--rule); margin-bottom: 4px; }
  .appt-row .fill--short { flex: 0 0 210px; }
  .days { display: flex; justify-content: space-between; margin-top: 30px; font-size: 14px; font-weight: 500; }
  .day { display: flex; align-items: center; gap: 3px; }
  .day .box { width: 14px; height: 11px; border: 2px solid var(--brand-blue); }
  .notice { margin-top: 32px; text-align: center; font-size: 13.5px; color: var(--muted); letter-spacing: .3px; }

  /* Contact side */
  .wave { position: absolute; inset: 0; width: 700px; height: 400px; }
  .person { position: absolute; left: 54px; top: 70px; }
  .person-name { font-size: 26px; font-weight: 700; color: var(--brand-blue); letter-spacing: .5px; }
  .person-role { font-size: 16px; font-weight: 600; color: var(--deep-teal); margin-top: -2px; }
  .address { margin-top: 14px; font-size: 15px; color: var(--ink); line-height: 1.3; }
  .contacts { list-style: none; margin-top: 12px; font-size: 15px; color: var(--ink); line-height: 1.35; }
  .contacts li { display: flex; align-items: center; gap: 12px; }
  .contacts svg { width: 14px; height: 14px; fill: var(--brand-blue); flex: none; }
  .card--contact .brand-name { position: absolute; right: 28px; top: 272px; font-size: 22px; color: var(--logo-light); }
</style>
</head>
<body>

<section class="card card--appointment">
  <div class="brand-name"><span class="mark"></span>The Brightwater Joint Centre</div>
  <div class="appt-form">
    <div class="appt-row"><span>NAME :</span><span class="fill"></span></div>
    <div class="appt-row"><span>DATE :</span><span class="fill"></span><span>TIME :</span><span class="fill fill--short"></span><span>AM/PM</span></div>
    <div class="days">
      <span class="day">SUN<span class="box"></span></span>
      <span class="day">MON<span class="box"></span></span>
      <span class="day">TUE<span class="box"></span></span>
      <span class="day">WED<span class="box"></span></span>
      <span class="day">THU<span class="box"></span></span>
      <span class="day">FRI<span class="box"></span></span>
      <span class="day">SAT<span class="box"></span></span>
    </div>
    <p class="notice">If unable to keep appointment, kindly give 24 hours notice.</p>
  </div>
</section>

<section class="card card--contact">
  <svg class="wave" viewBox="0 0 700 400" aria-hidden="true">
    <path d="M700 70 L700 400 L0 400 L0 388 C190 392 300 330 380 200 C440 100 520 62 700 70 Z" fill="var(--deep-teal)"/>
    <path d="M-10 382 C180 386 285 322 362 196 C420 100 490 66 560 62" fill="none" stroke="var(--brand-blue)" stroke-width="6"/>
    <path d="M-10 372 C170 376 272 314 348 190 C402 104 460 70 520 64" fill="none" stroke="var(--navy)" stroke-width="3"/>
  </svg>
  <div class="person">
    <div class="person-name">DANIEL HARTLEY</div>
    <div class="person-role">President</div>
    <div class="address">412 Harbour Crescent<br>Brightwater Bay, Easthollow 40218</div>
    <ul class="contacts">
      <li><svg viewBox="0 0 24 24"><path d="M6.6 10.8a15 15 0 0 0 6.6 6.6l2.2-2.2a1 1 0 0 1 1-.25 11.4 11.4 0 0 0 3.6.57 1 1 0 0 1 1 1V20a1 1 0 0 1-1 1A17 17 0 0 1 3 4a1 1 0 0 1 1-1h3.5a1 1 0 0 1 1 1c0 1.250.2 2.450.57 3.57a1 1 0 0 1-.25 1z"/></svg>555-204-7731</li>
      <li><svg viewBox="0 0 24 24"><path d="M7 1h10a2 2 0 0 1 2 2v18a2 2 0 0 1-2 2H7a2 2 0 0 1-2-2V3a2 2 0 0 1 2-2zm0 3v14h10V4z"/></svg>555-318-6402</li>
      <li><svg viewBox="0 0 24 24"><path d="M6 2h12v6H6zM3 9h18a1 1 0 0 1 1 1v8h-4v4H6v-4H2v-8a1 1 0 0 1 1-1zm5 7v4h8v-4z"/></svg>555-460-2918</li>
      <li><svg viewBox="0 0 24 24"><path d="M2 5h20v14H2zm2 2v.5l8 5 8-5V7z"/></svg>daniel@brightwaterjoint.com</li>
      <li><svg viewBox="0 0 24 24"><circle cx="12" cy="12" r="10"/></svg>www.brightwaterjoint.com</li>
    </ul>
  </div>
  <div class="brand-name">The Brightwater Joint Centre</div>
</section>

</body>
</html>
```